Business Card for premium dental clinic

We are a premium dental clinic based in Brasov, Romania with more than 15 year on the market, providing quality dental treatment made by a team of more specialized dentists, working with modern equipment as a solution to beautiful and healthy teeth.

Our current logo for the clinic use 2 square with colors black and gold - dr Ternisu - studio, using family fonts Bodoni, Myriad Pro and Segoe Print.
Depending on the printing we used some gold CMYK background or gold foil picture background or a gold gradient.
We want a business card:
- eye catching business card
- distinguished business card
- premium design
- to keep the color scheme of black and gold
- to attract the customers to spent time reading the information
- modern concept

```html
<!DOCTYPE html>
<html lang="en">
<head>
<meta charset="utf-8">
<title>dr Ternisu Studio – Business Card</title>
<link rel="stylesheet" href="https://fonts.googleapis.com/css2?family=Roboto:wght@400;500;700&display=swap">
<style>
  :root {
    --bg: #2b2b2c;
    --card: #141414;
    --gold: #e3a41c;
    --gold-light: #fbe37a;
    --gold-deep: #c98a12;
    --ink: #f2f2f2;
    --rule: #d9d9d9;
  }
  * { box-sizing: border-box; margin: 0; padding: 0; }
  html, body {
    width: 1200px; height: 1016px; overflow: hidden;
    background: var(--bg);
    font-family: "Roboto", Arial, sans-serif;
  }
  .sheet {
    position: relative; width: 1200px; height: 1016px;
    display: flex; flex-direction: column; align-items: center;
    justify-content: center; gap: 40px;
  }
  .card {
    position: relative; width: 700px; height: 400px;
    background: var(--card);
    box-shadow: 0 18px 40px rgba(0,0,0,.45);
  }

  /* Front */
  .card--front { display: flex; align-items: center; justify-content: center; }
  .brand {
    display: flex; align-items: center; gap: 18px;
    padding: 22px 30px;
    border: 1px solid #5a5a5a;
  }
  .brand__square {
    width: 46px; height: 46px;
    background: linear-gradient(135deg, var(--gold-deep), var(--gold-light) 50%, var(--gold-deep));
  }
  .brand__name {
    color: var(--ink); font-weight: 400; font-size: 38px; letter-spacing: .5px;
  }

  /* Back */
  .card--back { padding: 12px; }
  .frame {
    position: absolute; inset: 12px;
    border: 14px solid transparent;
    border-image: linear-gradient(90deg, var(--gold-deep), var(--gold-light) 20%, var(--gold) 40%, var(--gold-light) 60%, var(--gold-deep) 80%, var(--gold-light)) 1;
  }
  .contact {
    position: absolute; inset: 0;
    display: flex; flex-direction: column; align-items: center; justify-content: center;
    text-align: center;
  }
  .contact__name {
    color: var(--gold); font-weight: 700; font-size: 28px; letter-spacing: .5px;
    text-transform: uppercase; line-height: 1.1;
  }
  .contact__role {
    color: var(--gold); font-weight: 400; font-size: 15px; letter-spacing: .5px;
    text-transform: uppercase; margin-bottom: 14px;
  }
  .contact__rule { width: 370px; height: 1px; background: var(--rule); }
  .contact__line { color: var(--ink); font-size: 15px; line-height: 1.6; padding: 3px 0; }
  .contact__web { color: var(--ink); font-size: 15px; margin-top: 4px; }
</style>
</head>
<body>
<main class="sheet">
  <section class="card card--front" aria-label="Card front">
    <div class="brand">
      <span class="brand__square" aria-hidden="true"></span>
      <span class="brand__name">dr Ternisu</span>
    </div>
  </section>

  <section class="card card--back" aria-label="Card back">
    <div class="frame" aria-hidden="true"></div>
    <div class="contact">
      <p class="contact__name">Mara Ilescu</p>
      <p class="contact__role">President</p>
      <div class="contact__rule"></div>
      <p class="contact__line">48 Cedar Hill Road, Brasov, Romania 500130</p>
      <div class="contact__rule"></div>
      <p class="contact__line">P. 268-014-2283 E. hello@ternisustudio.com</p>
      <p class="contact__web">www.ternisustudio.com</p>
    </div>
  </section>
</main>
</body>
</html>
```